Dovin Sound 862 the new wave for sound to enlighten open ears

This is a music recording studio, we need pictures of a booth, random pictures of anything that will draw interest to a recording studio, we just need the website to reflect a music studio recording website. Apply generic information on the site that correlates with most music studio websites up to date. We want the modern style look that will entice eyes across the nation. Information should be easily accessible on the website. Dovin Sound 862 is owned by Marcellus Okafor located 5176 Bellweather Ln, Miramar, Fl, 33027. Email: Mokaforsound@trellomail.net and best contact number to date is 417-293-7041. The sound coming out of this location will be radio ready at all times, artist come in one way and come out with more wisdom than before. Its the new way to make music the appropriate way and bring the best out of those willing to reach their peak.

Target Market(s)

Recording Artist

Industry/Entity Type

Recording Studio

Coding

Coded - Design and coding required

Number of Pages Required

1 page

Font styles to use
Sans Serif

Requirements
Must have
• Anything that gives the site a music feel
Nice to have
• microphones, booths, studio mixing desk

```html
<!DOCTYPE html>
<html lang="en">
<head>
<meta charset="utf-8">
<title>Dovin Sound 862 — Recording Studio</title>
<link rel="stylesheet" href="https://fonts.googleapis.com/css2?family=Fugaz+One&family=Open+Sans:ital,wght@0,400;0,600;0,700;1,400&display=swap">
<style>
:root{
  --ink:#111;
  --text:#555;
  --muted:#8a8a8a;
  --gold:#d49a0c;
  --orange:#e0701a;
  --amber:#e8a020;
  --blue:#1ab0de;
  --tangerine:#e8861c;
  --green:#8cd86a;
  --card:#ececec;
  --peach:#f8d5b8;
  --field:#f3c29c;
  --footer:#1b1b1b;
  --white:#fff;
}
*{box-sizing:border-box;margin:0;padding:0}
html,body{width:1200px;height:3727px;overflow:hidden}
body{font-family:"Open Sans",Arial,sans-serif;color:var(--text);background:var(--white);position:relative}
section,header,footer{position:absolute;left:0;width:1200px}
.abs{position:absolute}
.center{left:0;width:1200px;text-align:center}

/* hero */
.hero{top:0;height:676px;overflow:hidden}
.hero-photo{position:absolute;inset:0;background:radial-gradient(ellipse at 50% 35%,#5b4a5a 0%,#3a2c3a 35%,#1f1820 75%),#241b24}
.hero-photo::after{content:"";position:absolute;left:0;right:0;bottom:0;height:260px;background:linear-gradient(180deg,rgba(90,50,30,0) 0%,rgba(110,60,35,.55) 100%)}
.brand{position:absolute;left:162px;top:44px;font-size:24px;font-weight:600;color:var(--white);letter-spacing:.2px}
.menu{position:absolute;left:1003px;top:50px}
.hero-title{top:196px;font-family:"Fugaz One",sans-serif;font-style:italic;font-size:62px;color:var(--white);letter-spacing:2px}
.hero-copy{top:280px;left:300px;width:600px;text-align:center;color:#e6e0e6;font-size:13px;line-height:19px}
.btn-gold{left:517px;top:375px;width:169px;height:42px;background:var(--gold);color:var(--white);font-size:12px;line-height:42px;text-align:center;text-transform:uppercase}
.social-rail{left:0;top:288px}
.social-rail span{display:block;width:32px;height:33px}

/* headings */
.sec-title{font-size:31px;font-weight:600;color:var(--ink);letter-spacing:.5px}
.para{font-size:11.5px;line-height:19px;color:var(--muted);text-align:center}
.link-more{font-size:11px;color:var(--amber)}

/* welcome */
.welcome{top:676px;height:410px}
.kicker{color:var(--amber);font-size:20px}

/* tiles */
.tiles{display:flex}
.tile{position:relative;height:100%}
.tile-dark{background:#2a2623;color:#d8d2cc;text-align:center}
.tile-title{color:var(--amber);font-size:16px;font-weight:600;text-transform:uppercase}
.tile-text{font-size:12px;line-height:20px}

/* packages */
.card{top:2300px;width:282px;height:313px;background:var(--card)}
.card-head{height:55px;line-height:55px;text-align:center;color:var(--white);font-size:13px;font-weight:600;text-transform:uppercase}
.card ul{list-style:none;padding:22px 22px 0 32px}
.card li{position:relative;font-size:11.5px;line-height:18px;color:#444;margin-bottom:12px;padding-left:14px}
.card li::before{content:"";position:absolute;left:0;top:6px;width:6px;height:6px;border-radius:50%;background:var(--amber)}
.card-btn{position:absolute;left:76px;top:258px;width:130px;height:36px;line-height:36px;text-align:center;color:var(--white);font-size:11px;border-radius:3px}

/* testimonial */
.testimonial{top:2745px;height:452px;overflow:hidden}
.test-photo{position:absolute;inset:0;background:linear-gradient(90deg,#2a2420 0%,#3c342d 40%,#2e2824 70%,#1f1c19 100%)}
.test-photo::after{content:"";position:absolute;inset:0;background:rgba(15,12,10,.45)}
.avatar{left:532px;top:82px;width:132px;height:130px;border:4px solid var(--white);background:linear-gradient(160deg,#c8a98a,#7c6650)}
.quote{top:283px;left:270px;width:660px;text-align:center;color:#d8d2cc;font-size:12px;line-height:20px;font-style:italic}
.person{top:336px;font-size:20px;color:var(--white)}
.role{top:368px;font-size:12px;color:#bdb5ad}

/* contact */
.contact{top:3197px;height:380px;background:var(--peach)}
.c-head{font-size:15px;font-weight:600;color:#333}
.c-item{left:162px;font-size:12px;color:#333;display:flex;align-items:center;gap:14px}
.field{height:30px;background:var(--field);border:1px solid #eab48a;font-size:11px;color:#a0785a;padding:0 14px;line-height:28px}
.send{left:698px;top:253px;width:159px;height:40px;background:var(--orange);color:var(--white);font-size:12px;line-height:40px;text-align:center;border-radius:3px}

/* footer */
.footer{top:3577px;height:150px;background:var(--footer)}
.f-dot{top:20px;width:22px;height:22px;border-radius:50%;background:var(--white)}
.f-nav{top:64px;font-size:11px;color:#ccc;letter-spacing:.3px}
.f-rule{top:107px;left:0;width:1200px;height:1px;background:#3a3a3a}
.f-copy{top:118px;left:162px;font-size:10px;color:#999}
</style>
</head>
<body>

<header class="hero">
  <div class="hero-photo" role="img" aria-label="Dimly lit recording studio control room with mixing desk and monitor speakers"></div>
  <div class="brand">Dovin Sound 862</div>
  <svg class="menu" width="26" height="22" viewBox="0 0 26 22"><rect y="2" width="26" height="3.5" fill="#fff"/><rect y="9" width="26" height="3.5" fill="#fff"/><rect y="16" width="26" height="3.5" fill="#fff"/></svg>
  <div class="abs social-rail">
    <span style="background:#3b5998"></span>
    <span style="background:#dd4b39"></span>
    <span style="background:#1da1f2"></span>
  </div>
  <h1 class="abs center hero-title">Music Just For You!</h1>
  <p class="abs hero-copy">Radio ready sound from the first take to the final master. Artists walk in with a vision and leave with a record they are proud of, tracked, mixed and polished in rooms built for music.</p>
  <div class="abs btn-gold">View More</div>
</header>

<section class="welcome">
  <h2 class="abs center sec-title" style="top:36px">WELCOME</h2>
  <div class="abs center kicker" style="top:80px">to our studio</div>
  <h3 class="abs center" style="top:130px;font-size:24px;font-weight:600;color:var(--ink)">Create your best record!</h3>
  <p class="abs para" style="top:172px;left:268px;width:664px">Dovin Sound 862 is a full service recording studio for singers, rappers, bands and producers. Our treated booths, analog outboard and experienced engineers give every session a clear, warm and powerful sound. Book a block of hours, bring your ideas and let our team help you shape them into songs that stand up next to anything on the radio. From first demo to final master, we stay with you at every step.</p>
  <div class="abs center link-more" style="top:318px">View Our Projects</div>
  <svg class="abs" style="left:589px;top:336px" width="22" height="12" viewBox="0 0 22 12"><polyline points="1,1 11,10 21,1" fill="none" stroke="#e8a020" stroke-width="1.5"/></svg>
</section>

<section class="tiles" style="top:1086px;height:226px">
  <div class="tile" style="width:300px;background:linear-gradient(160deg,#3d4658,#1a1f2a)" role="img" aria-label="Film poster for a superhero action movie"></div>
  <div class="tile" style="width:300px;background:linear-gradient(180deg,#1d7fc9,#0d4f8f)" role="img" aria-label="Poster for an animated underwater family film"></div>
  <div class="tile tile-dark" style="width:300px">
    <div class="abs tile-title" style="top:46px;left:0;width:300px">Sample Text Here</div>
    <p class="abs tile-text" style="top:76px;left:40px;width:220px">Scores, soundtracks and songs recorded and mixed right here in our rooms.</p>
    <div class="abs" style="top:160px;left:110px;width:80px;height:26px;line-height:26px;background:#5a4a2a;color:#fff;font-size:11px">View More</div>
  </div>
  <div class="tile" style="width:300px;background:linear-gradient(160deg,#e3b070,#8a5a2c)" role="img" aria-label="Poster for an animated prehistoric family comedy"></div>
</section>

<section style="top:1312px;height:345px">
  <h2 class="abs center sec-title" style="top:90px">STUDIO SERVICES</h2>
  <p class="abs para" style="top:138px;left:273px;width:654px;color:#666">Tracking, editing, mixing and mastering under one roof. We record vocals in an isolated booth, capture live instruments in a tuned live room and finish each project on calibrated monitors. Production, beat making and artist development sessions are also available for those who want a full team behind them.</p>
  <div class="abs center link-more" style="top:272px">View Our Services</div>
  <svg class="abs" style="left:589px;top:290px" width="22" height="12" viewBox="0 0 22 12"><polyline points="1,1 11,10 21,1" fill="none" stroke="#e8a020" stroke-width="1.5"/></svg>
</section>

<section class="tiles" style="top:1657px;height:310px">
  <div class="tile" style="width:400px;background:linear-gradient(150deg,#8a5a3a,#3a2a20)" role="img" aria-label="Condenser microphone in front of studio rack gear"></div>
  <div class="tile tile-dark" style="width:400px;background:#2f2b27">
    <div class="abs tile-title" style="top:90px;left:0;width:400px">Mixing &amp; Mastering</div>
    <p class="abs tile-text" style="top:124px;left:80px;width:240px">Balanced, loud and clean mixes that translate on every speaker.</p>
    <div class="abs" style="top:185px;left:150px;width:100px;height:30px;line-height:28px;border:1px solid #c98a2a;color:#e8a020;font-size:11px">Read More »</div>
  </div>
  <div class="tile" style="width:400px;background:linear-gradient(150deg,#4a4a4a,#151515)" role="img" aria-label="Vocalist with headphones singing into a microphone in a recording booth"></div>
</section>

<section style="top:1967px;height:778px">
  <h2 class="abs center sec-title" style="top:78px">AFFORDABLE PACKAGES</h2>
  <p class="abs para" style="top:134px;left:268px;width:664px;color:#666">Flexible rates for every stage of your career. Pay by the hour for quick sessions, lock in a membership for steady studio time or book a mix down package to finish your project with our engineers.</p>
  <div class="abs center link-more" style="top:250px">View Our Price List</div>
  <svg class="abs" style="left:589px;top:268px" width="22" height="12" viewBox="0 0 22 12"><polyline points="1,1 11,10 21,1" fill="none" stroke="#e8a020" stroke-width="1.5"/></svg>
</section>

<div class="abs card" style="left:161px">
  <div class="card-head" style="background:var(--blue)">Recording Price</div>
  <ul>
    <li>$80 per hour minimum 4 hours required</li>
    <li>$75 per hour minimum 8 hours required</li>
    <li>$70 per hour minimum 12 hours required</li>
    <li>$90 for individual hours, packages recommended</li>
  </ul>
  <div class="card-btn" style="background:#1a98c4">Subscribe</div>
</div>
<div class="abs card" style="left:459px">
  <div class="card-head" style="background:var(--tangerine)">Memberships Deals</div>
  <ul>
    <li>$1500, get 48 recording hours in addition to 24 hours mix down</li>
    <li>$2500, get 72 recording hours in addition to 48 hours mix down</li>
    <li>$3500, get 96 recording hours in addition to 72 hours mix down</li>
  </ul>
  <div class="card-btn" style="background:#c8650e">Subscribe</div>
</div>
<div class="abs card" style="left:757px">
  <div class="card-head" style="background:var(--green)">Mix Down</div>
  <ul>
    <li>$50 per hour minimum 4 hours required</li>
    <li>$45 per hour minimum 8 hours required</li>
    <li>$40 per hour minimum 12 hours required</li>
    <li>$60 for individual hours, packages recommended</li>
  </ul>
  <div class="card-btn" style="background:#6bb84c">Subscribe</div>
</div>

<section class="testimonial">
  <div class="test-photo" role="img" aria-label="Blurred studio microphone and recording equipment"></div>
  <div class="abs avatar" role="img" aria-label="Portrait of a studio client"></div>
  <svg class="abs" style="left:164px;top:212px" width="18" height="34" viewBox="0 0 18 34"><polyline points="16,2 2,17 16,32" fill="none" stroke="#fff" stroke-width="2"/></svg>
  <svg class="abs" style="left:1018px;top:212px" width="18" height="34" viewBox="0 0 18 34"><polyline points="2,2 16,17 2,32" fill="none" stroke="#fff" stroke-width="2"/></svg>
  <p class="abs quote">"The engineers here pulled a sound out of my band that we never heard before. Every session was focused, relaxed and productive, and the final mixes went straight to radio without a single change. We will be back for the next album."</p>
  <div class="abs center person">Dario Venn</div>
  <div class="abs center role">Bass Guitar</div>
</section>

<section class="contact">
  <div class="abs c-head" style="left:162px;top:92px">To Reach US:</div>
  <div class="abs c-item" style="top:138px">
    <svg width="14" height="18" viewBox="0 0 14 18"><path d="M7 0C3.1 0 0 3.1 0 7c0 5 7 11 7 11s7-6 7-11c0-3.9-3.1-7-7-7z" fill="#e0701a"/><circle cx="7" cy="7" r="2.6" fill="#f8d5b8"/></svg>
    <span>5176 Bellweather Ln, Miramar, Fl, 33027</span>
  </div>
  <div class="abs c-item" style="top:178px">
    <svg width="16" height="16" viewBox="0 0 16 16"><path d="M3 1l3 0 1 4-2 1c1 2 3 4 5 5l1-2 4 1 0 3c0 1-1 2-2 2C7 15 1 9 1 3c0-1 1-2 2-2z" fill="#e0701a"/></svg>
    <span>417-293-7041</span>
  </div>
  <div class="abs c-item" style="top:218px">
    <svg width="18" height="13" viewBox="0 0 18 13"><rect width="18" height="13" fill="#e0701a"/><polyline points="0,0 9,7 18,0" fill="none" stroke="#f8d5b8" stroke-width="1.5"/></svg>
    <span>Mokaforsound@trellomail.net</span>
  </div>

  <div class="abs c-head" style="left:497px;top:92px">To Say Hello:</div>
  <div class="abs field" style="left:497px;top:126px;width:243px">Your Name</div>
  <div class="abs field" style="left:790px;top:126px;width:246px">Your Email</div>
  <div class="abs field" style="left:497px;top:191px;width:539px">Message</div>
  <div class="abs send">Send Your Message</div>
</section>

<footer class="footer">
  <div class="abs f-dot" style="left:545px"></div>
  <div class="abs f-dot" style="left:589px"></div>
  <div class="abs f-dot" style="left:633px"></div>
  <div class="abs center f-nav">HOME &nbsp;|&nbsp; FEATURES &nbsp;|&nbsp; STUDIO &nbsp;|&nbsp; EQUIPMENT &nbsp;|&nbsp; ENGINEERS &nbsp;|&nbsp; SERVICES &nbsp;|&nbsp; ABOUT &nbsp;|&nbsp; CONTACTS</div>
  <div class="abs f-rule"></div>
  <div class="abs f-copy">Dovin Sound 862 © 2017 All rights reserved.</div>
</footer>

</body>
</html>
```